Water Delivery Service Website

We are working with BrivoNessé. They are a water delivery company and in need of a new website design.
Some sites to use for inspiration:
https://www.pelmoriston.example/home
https://www.quintalbrook.example/en/home3
https://www.drevik.example
https://www.tormaxel.example
Thank you for taking the time to consider designing a website for us. We are web developers based in Stockton, CA, USA. Most of our projects go through the same process. Understanding this process may help you win a project with us. We custom-code all of our websites in-house. We don’t have any requirements as to what tools you use for your design, but we prefer Figma files. For any design that we label as four-stars, we send it to the client for review. The client picks the final design they want us to use. Once we complete this process, we will continue to show additional clients all the four-star sites and purchase them later. Your designs will have multiple chances to sell. For better chances of success, we ask that you follow these guidelines.
IMAGES:
If you use any images or icons in the design, we ask that you have a link to the asset so we can purchase the image/icon. Most of the designs we submit do not have the customer’s images on them unless they have some great images. Be creative; show us the feeling you are trying to portray with your image choices. Use any royalty-free site you choose. We subscribe to Vantrel and mainly use their images, but we can purchase images outside of Vantrel.
PLEASE NOTE: we will not submit designs to clients with watermarks on the images.
FONTS:
We ask that you identify the fonts used in the design. This can be done in a message if you want. We typically use Google Fonts and Vantrel Fonts.
CONTENT:
We're always open to different content and ideas. We often submit designs with stock images so the client can see our vision. We typically take pictures after the website launch to use their images with our vision. Lorem Ipsum is fine for paragraphs, but we ask that you write the headers in correct English. We want to be able to show the vision and identify the sections of the website.
INSPIRATION:
We typically add a couple of links in the brief of websites we like to help you get started in your design.
REVISIONS:
We do not often ask for revisions of the designs unless we see something in the design that may not appeal to the client. If there are slight changes that we want to make, we do that in the development process.
FEEDBACK:
We rarely give feedback on designs during the design process. We are working on many website projects and do not have the time to provide feedback. We usually respond if your request is well thought out and asks specific questions, but a note asking “feedback, please” usually goes unanswered.

```html
<!DOCTYPE html>
<html lang="en">
<head>
<meta charset="utf-8">
<title>BrivoNessé – Water Delivery</title>
<link rel="stylesheet" href="https://fonts.googleapis.com/css2?family=Poppins:wght@400;500;600;700&display=swap">
<style>
:root{
  --blue:#1f97e2;
  --blue-deep:#1479c4;
  --navy:#1c1d5a;
  --ink:#17192b;
  --muted:#6c7280;
  --pale:#eef6fc;
  --white:#ffffff;
  --star:#f0a81c;
}
*{box-sizing:border-box;margin:0;padding:0}
html,body{width:1200px;height:4721px;overflow:hidden}
body{position:relative;font-family:"Poppins",sans-serif;color:var(--ink);background:var(--white)}
.abs{position:absolute}
a{color:inherit;text-decoration:none}

/* top bar */
.topbar{left:549px;top:0;width:651px;height:50px;background:var(--navy);clip-path:polygon(0 0,100% 0,100% 100%,40px 100%);color:#fff;font-size:15px;display:flex;align-items:center;gap:22px;padding-left:52px}
.topbar .sep{width:1px;height:18px;background:#8c8fc0}
.topbar .dots{display:flex;gap:10px}
.topbar .dots span{width:10px;height:10px;border-radius:50%;background:#fff}
.ico{display:inline-flex;align-items:center;gap:8px}

/* header */
.logo{font-weight:600;font-size:40px;color:var(--blue);display:flex;align-items:center;gap:10px;letter-spacing:-0.5px}
.logo .dot{width:22px;height:22px;border-radius:50%;background:var(--navy)}
.site-logo{left:110px;top:28px}
.nav{left:520px;top:72px;display:flex;align-items:center;gap:40px;font-size:16px;font-weight:500}
.nav .active{color:var(--blue)}
.btn{display:inline-flex;align-items:center;justify-content:center;background:var(--blue);color:#fff;font-weight:600;border-radius:30px}
.nav .btn{width:116px;height:42px;font-size:14px;box-shadow:0 0 0 3px #bfe0f6}

/* hero */
.hero-welcome{left:111px;top:188px;font-size:19px;font-weight:500}
.hero-title{left:108px;top:218px;font-size:52px;line-height:62px;font-weight:700;color:var(--navy)}
.hero-title .hl{color:var(--blue)}
.hero-text{left:110px;top:412px;width:440px;font-size:18px;line-height:35px}
.hero-cta{left:112px;top:503px;width:232px;height:48px;font-size:17px;box-shadow:0 0 0 4px #cfe7f8}
.hero-photo{left:560px;top:138px;width:520px;height:540px;border-radius:260px 260px 0 0;background:linear-gradient(160deg,#cfe3f1 0%,#5f8fbf 45%,#1f57b8 100%)}
.splash{left:0;top:580px;width:1200px;height:340px;background:linear-gradient(180deg,rgba(255,255,255,0) 0%,#bfe0f5 30%,#3ea4e6 65%,var(--blue) 100%)}
.blue-band{left:0;top:915px;width:1200px;height:472px;background:linear-gradient(180deg,var(--blue) 0%,#2a9ce5 100%)}

/* choose */
.section-title{left:0;width:1200px;text-align:center;font-size:42px;font-weight:600;color:var(--blue)}
.choose-title{top:935px;color:#fff}
.choose-text{left:220px;top:1022px;width:760px;text-align:center;color:#fff;font-size:16px;line-height:31px;font-weight:500}
.card{top:1156px;width:295px;height:420px;background:#fff;border-radius:12px;box-shadow:0 10px 30px rgba(20,60,100,.14);text-align:center;overflow:hidden}
.card .photo{height:231px}
.card .badge{position:absolute;left:121px;top:196px;width:54px;height:54px;border-radius:50%;background:var(--blue);border:4px solid #fff;display:flex;align-items:center;justify-content:center}
.card h3{margin-top:36px;font-size:18px;font-weight:600}
.card p{margin:10px auto 0;width:265px;font-size:14px;line-height:26px;color:#4a4e5a}

/* steps */
.steps-title{top:1662px}
.step{top:1765px;width:250px;text-align:center}
.step svg{display:block;margin:0 auto}
.step h4{margin-top:22px;font-size:20px;font-weight:600;color:var(--blue)}
.step p{margin:12px auto 0;width:225px;font-size:13.5px;line-height:26px;color:#4a4e5a}
.dash{top:1860px}

/* promo */
.promo{left:79px;top:2198px;width:1044px;height:427px;background:var(--pale);border-radius:30px;overflow:hidden}
.promo .photo{position:absolute;left:0;top:0;width:489px;height:427px;background:linear-gradient(135deg,#e8eef3 0%,#9fb6c8 40%,#2f6fa8 75%,#1d4d80 100%)}
.promo h2{position:absolute;left:555px;top:52px;font-size:44px;line-height:57px;font-weight:600;color:var(--blue)}
.promo p{position:absolute;left:555px;top:170px;width:440px;font-size:15.5px;line-height:31px;color:#3d414d}
.promo .btn{position:absolute;left:555px;top:314px;width:154px;height:48px;font-size:17px}

/* testimonials */
.testi-title{top:2696px}
.quote{width:311px;background:#fff;border:2px solid #e3e6ea;padding:30px 18px 0 18px;box-shadow:0 6px 18px rgba(0,0,0,.05)}
.quote .stars{color:var(--star);font-size:20px;letter-spacing:1px}
.quote p{margin-top:14px;font-size:15.5px;line-height:27.5px}
.quote .who{margin-top:16px;display:flex;align-items:center;gap:14px}
.quote .avatar{width:64px;height:64px;border-radius:50%;background:linear-gradient(135deg,#c9b29f,#5b4a3d)}
.quote .name{font-weight:700;font-size:16px}
.quote .loc{font-size:14px;color:var(--muted)}

/* contact */
.contact-bg{left:0;top:3270px;width:1200px;height:730px;background:linear-gradient(180deg,#d9eefb 0%,#f5fbff 30%,#ffffff 70%)}
.contact-title{top:3330px}
.contact-text{left:190px;top:3400px;width:820px;text-align:center;font-size:16px;line-height:29px;color:#3d414d}
.form-card{left:192px;top:3495px;width:816px;height:431px;background:#fff;box-shadow:0 8px 30px rgba(20,60,100,.12)}
.form-card .logo{position:absolute;left:36px;top:28px;font-size:34px;opacity:.45}
.form-card .mini{position:absolute;left:36px;top:90px}
.form-card .kicker{position:absolute;left:36px;top:134px;font-size:14px}
.form-card h3{position:absolute;left:36px;top:156px;font-size:21px;font-weight:700}
.form-card .lead{position:absolute;left:36px;top:194px;width:255px;font-size:11.5px;line-height:21px;color:#555}
.form-card .call{position:absolute;left:36px;top:290px;display:flex;align-items:center;gap:14px}
.form-card .call .c{width:44px;height:44px;border-radius:50%;border:3px solid var(--blue);display:flex;align-items:center;justify-content:center}
.form-card .call small{display:block;color:var(--blue);font-size:14px}
.form-card .call b{font-size:21px}
.field{position:absolute;background:#eef0f2;font-size:12px;color:#555;padding:14px 16px}
.submit{position:absolute;left:356px;top:312px;width:138px;height:52px;font-size:19px;box-shadow:0 0 0 4px #d6ebf9}
.agree{position:absolute;left:520px;top:328px;font-size:13px;color:#555;display:flex;align-items:center;gap:10px}
.agree i{width:12px;height:12px;border-radius:50%;border:3px solid #cfe5f6;background:var(--blue)}
.form-card .rule{position:absolute;left:36px;bottom:0;width:744px;height:3px;background:var(--blue)}

/* footer */
.foot-water{left:0;top:3990px;width:1200px;height:340px;background:linear-gradient(180deg,rgba(255,255,255,0) 0%,#a6d5f2 30%,#3aa1e6 65%,var(--blue) 100%)}
.footer{left:0;top:4328px;width:1200px;height:393px;background:linear-gradient(180deg,var(--blue) 0%,#1a88d6 100%);color:#fff}
.footer .logo{position:absolute;left:110px;top:80px;color:#fff;font-size:44px}
.footer .logo .dot{background:#fff}
.footer .social{position:absolute;left:112px;top:170px;display:flex;gap:20px}
.footer .social span{width:26px;height:26px;border-radius:50%;border:2px solid #cfe8fa}
.footer .social span:first-child{background:#fff}
.fcol{position:absolute;top:52px}
.fcol h5{font-size:20px;font-weight:600;margin-bottom:14px}
.fcol li{list-style:none;font-size:15px;line-height:34.5px;padding-left:8px}
.fcol .row{display:flex;align-items:flex-start;gap:14px;font-size:15px;line-height:23px;margin-bottom:16px}
.fcol .pin{width:32px;height:32px;border-radius:50%;background:#fff;display:flex;align-items:center;justify-content:center;flex:none}
.footer .divider{position:absolute;left:110px;top:298px;width:980px;height:1px;background:rgba(255,255,255,.55)}
.footer .copy{position:absolute;left:0;top:332px;width:1200px;text-align:center;font-size:15px;font-weight:500}
</style>
</head>
<body>

<!-- top bar -->
<div class="abs topbar">
  <span class="ico"><svg width="14" height="14" viewBox="0 0 24 24" fill="#fff"><path d="M6.6 10.8a15.1 15.1 0 0 0 6.6 6.6l2.2-2.2c.3-.3.7-.4 1-.2 1.1.4 2.3.6 3.6.6.6 0 1 .4 1 1V20c0 .6-.4 1-1 1A17 17 0 0 1 3 4c0-.6.4-1 1-1h3.5c.6 0 1 .4 1 1 0 1.3.2 2.5.6 3.6.1.3 0 .7-.2 1z"/></svg>+1 555 014 7720</span>
  <span class="sep"></span>
  <span class="ico"><svg width="14" height="12" viewBox="0 0 24 20" fill="#fff"><path d="M2 2h20v16H2z" /><path d="M2 2l10 8 10-8" stroke="#1c1d5a" stroke-width="2" fill="none"/></svg>info@brivonesse.example</span>
  <span class="sep"></span>
  <span class="dots"><span></span><span></span><span></span></span>
</div>

<!-- header -->
<div class="abs logo site-logo"><span class="dot"></span>BrivoNessé</div>
<nav class="abs nav">
  <a class="active" href="#">Home</a>
  <a href="#">About</a>
  <a href="#">Water Delivery</a>
  <a href="#">Testimonial</a>
  <a class="btn" href="#">Contact Us</a>
</nav>

<!-- hero -->
<div class="abs splash" role="img" aria-label="Splashing water wave with droplets"></div>
<div class="abs blue-band"></div>
<div class="abs hero-photo" role="img" aria-label="Smiling delivery worker in a blue cap carrying a large water jug on his shoulder"></div>
<div class="abs hero-welcome">WELCOME TO</div>
<h1 class="abs hero-title"><span class="hl">BrivoNessé –</span><br>Refreshing Every<br>Moment</h1>
<p class="abs hero-text">Stay hydrated with the finest water, delivered on your schedule.</p>
<a class="abs btn hero-cta" href="#">Try BrivoNessé Today</a>

<!-- choose -->
<h2 class="abs section-title choose-title">Choose BrivoNessé Water</h2>
<p class="abs choose-text">Duis aute irure dolor in reprehenderit in voluptate velit esse cillum dolore eu fugiat nulla pariatur. Excepteur sint occaecat cupidatat non proident, sunt in culpa qui officia deserunt mollit anim id est laborum.</p>

<div class="abs card" style="left:112px">
  <div class="photo" role="img" aria-label="Person drinking from a water bottle under a clear sky" style="background:linear-gradient(160deg,#6fa6d6,#c9a27e 60%,#8c5b3c)"></div>
  <span class="badge"><svg width="22" height="26" viewBox="0 0 22 26"><path d="M11 1C7 7 3 11 3 16a8 8 0 0 0 16 0c0-5-4-9-8-15z" fill="#fff"/></svg></span>
  <h3>Know Your Water</h3>
  <p>Lorem ipsum dolor sit amet, consectetur adipiscing elit, sed do eiusmod tempor incididunt ut labore et dagna aliqua.</p>
</div>
<div class="abs card" style="left:452px">
  <div class="photo" role="img" aria-label="Stacked water delivery jugs in a warehouse" style="background:linear-gradient(160deg,#d7ecf8,#5fa8dc 55%,#1d5f9e)"></div>
  <span class="badge"><svg width="20" height="26" viewBox="0 0 20 26"><rect x="7" y="1" width="6" height="4" fill="#fff"/><path d="M5 6h10l2 4v14H3V10z" fill="#fff"/></svg></span>
  <h3>Get Your Water</h3>
  <p>Lorem ipsum dolor sit amet, consectetur adipiscing elit, sed do eiusmod tempor incididunt ut labore et dagna aliqua.</p>
</div>
<div class="abs card" style="left:793px">
  <div class="photo" role="img" aria-label="Water pouring from a bottle into a glass" style="background:linear-gradient(160deg,#eaf5fc,#7fc0ea 50%,#1a6fb5)"></div>
  <span class="badge"><svg width="24" height="26" viewBox="0 0 24 26"><path d="M12 1C9 6 6 9 6 13a6 6 0 0 0 12 0c0-4-3-7-6-12z" fill="#fff"/><path d="M2 22h20" stroke="#fff" stroke-width="3"/></svg></span>
  <h3>Choose Responsible Water</h3>
  <p>Lorem ipsum dolor sit amet, consectetur adipiscing elit, sed do eiusmod tempor incididunt ut labore et dagna aliqua.</p>
</div>

<!-- steps -->
<h2 class="abs section-title steps-title">How Water Delivery Works</h2>
<svg class="abs dash" style="left:280px" width="680" height="80" viewBox="0 0 680 80" fill="none" stroke="#333" stroke-width="1.5" stroke-dasharray="6 5">
  <path d="M0 10 C50 25 90 30 130 40"/>
  <path d="M245 0 C300 10 340 40 370 60"/>
  <path d="M500 40 C540 15 580 0 640 5"/>
</svg>

<div class="abs step" style="left:93px">
  <svg width="140" height="200" viewBox="0 0 140 200"><path d="M70 2C50 40 2 80 2 120a68 68 0 0 0 136 0C138 80 90 40 70 2z" fill="#1f97e2"/><g stroke="#fff" stroke-width="3" fill="none"><rect x="54" y="95" width="32" height="40" rx="3"/><rect x="60" y="82" width="20" height="13"/><path d="M54 112h32"/></g><circle cx="70" cy="181" r="17" fill="#1c1d5a" stroke="#fff" stroke-width="3"/><text x="70" y="187" text-anchor="middle" font-family="Poppins,sans-serif" font-size="17" fill="#fff">01</text></svg>
  <h4>Build Your Order</h4>
  <p>Duis aute irure dolor in reprehenderit in voluptate velit eu fugiat nulla pariatur.</p>
</div>
<div class="abs step" style="left:346px">
  <svg width="140" height="200" viewBox="0 0 140 200"><path d="M70 2C50 40 2 80 2 120a68 68 0 0 0 136 0C138 80 90 40 70 2z" fill="#1f97e2"/><g stroke="#fff" stroke-width="3" fill="none"><circle cx="66" cy="105" r="17"/><path d="M58 105l6 6 11-12"/><path d="M44 128h44v10H44z"/><circle cx="54" cy="142" r="4"/><circle cx="80" cy="142" r="4"/></g><circle cx="70" cy="181" r="17" fill="#1c1d5a" stroke="#fff" stroke-width="3"/><text x="70" y="187" text-anchor="middle" font-family="Poppins,sans-serif" font-size="17" fill="#fff">02</text></svg>
  <h4>Get It Delivered</h4>
  <p>Duis aute irure dolor in reprehenderit in voluptate velit eu fugiat nulla pariatur.</p>
</div>
<div class="abs step" style="left:600px">
  <svg width="140" height="200" viewBox="0 0 140 200"><path d="M70 2C50 40 2 80 2 120a68 68 0 0 0 136 0C138 80 90 40 70 2z" fill="#1f97e2"/><g stroke="#fff" stroke-width="3" fill="none"><rect x="62" y="84" width="16" height="10"/><path d="M58 94h24l6 10v38H52v-38z"/></g><circle cx="70" cy="181" r="17" fill="#1c1d5a" stroke="#fff" stroke-width="3"/><text x="70" y="187" text-anchor="middle" font-family="Poppins,sans-serif" font-size="17" fill="#fff">03</text></svg>
  <h4>Put Out Empty Bottles</h4>
  <p>Duis aute irure dolor in reprehenderit in voluptate velit eu fugiat nulla pariatur.</p>
</div>
<div class="abs step" style="left:853px">
  <svg width="140" height="200" viewBox="0 0 140 200"><path d="M70 2C50 40 2 80 2 120a68 68 0 0 0 136 0C138 80 90 40 70 2z" fill="#1f97e2"/><g stroke="#fff" stroke-width="3" fill="none"><path d="M42 100h8l8 30h30l6-22H54"/><circle cx="62" cy="140" r="4"/><circle cx="84" cy="140" r="4"/><circle cx="78" cy="98" r="11"/><path d="M73 98l4 4 7-7"/></g><circle cx="70" cy="181" r="17" fill="#1c1d5a" stroke="#fff" stroke-width="3"/><text x="70" y="187" text-anchor="middle" font-family="Poppins,sans-serif" font-size="17" fill="#fff">04</text></svg>
  <h4>Update Your Order</h4>
  <p>Duis aute irure dolor in reprehenderit in voluptate velit eu fugiat nulla pariatur.</p>
</div>

<!-- promo -->
<section class="abs promo">
  <div class="photo" role="img" aria-label="Smiling delivery worker holding a case of water bottles in front of a delivery truck"></div>
  <h2>50% off up to<br>$50 + FREE DELIVERY</h2>
  <p>Lorem ipsum dolor sit amet, consectetur adipiscing elit, sed do eiusmod tempor incididunt ut labore et dolore mod tempor incididunt ut lamod tempor incididunt ut lamagna aliqua.</p>
  <a class="btn" href="#">Get Started</a>
</section>

<!-- testimonials -->
<h2 class="abs section-title testi-title">What Our Customer Says</h2>
<div class="abs quote" style="left:104px;top:2796px;height:340px">
  <div class="stars">★★★★★</div>
  <p>Temporibus autem quibusdam et aut officiis debitis aut rerum neus saepe facere mus, onis voluptas eveniet ut et voluptates repudae sint et molestiae non lorem recusadae.</p>
  <div class="who"><span class="avatar" role="img" aria-label="Customer portrait"></span><div><div class="name">Corwin Halsey</div><div class="loc">United States</div></div></div>
</div>
<div class="abs quote" style="left:445px;top:2836px;height:339px">
  <div class="stars">★★★★★</div>
  <p>Itaque earum rerum hic tenetur a sapiene delectus, ut aut reiciels volupatibus maiores alias conse uatur aut perferndis doloribus asperiores reiciendis voluptatbus repellat</p>
  <div class="who"><span class="avatar" role="img" aria-label="Customer portrait" style="background:linear-gradient(135deg,#e6cdb8,#9a6c4c)"></span><div><div class="name">Odette</div><div class="loc">United States</div></div></div>
</div>
<div class="abs quote" style="left:784px;top:2796px;height:340px">
  <div class="stars">★★★★★</div>
  <p>At vero eos et accusamus et iusto odio dignissimos ducimus qui blaiis praesentium voluptum deleniti atque corrupti quos dolores et quas occaecati cupie non provident</p>
  <div class="who"><span class="avatar" role="img" aria-label="Customer portrait" style="background:linear-gradient(135deg,#9aa3a8,#3b4246)"></span><div><div class="name">Marlon Fenwick</div><div class="loc">United States</div></div></div>
</div>

<!-- contact -->
<div class="abs contact-bg"></div>
<h2 class="abs section-title contact-title">Get In Touch with us</h2>
<p class="abs contact-text">Lorem ipsum dolor sit amet, consectetur adipiscing elit, sed do eiusmod tempor incididunt ut labore et dolore magna aliquad exercitation ullamco laboris nisi ut aliquip ex ea commodo consequat.</p>
<section class="abs form-card">
  <div class="logo"><span class="dot" style="background:#9aa0c8"></span>BrivoNessé</div>
  <svg class="mini" width="28" height="28" viewBox="0 0 28 28" fill="none" stroke="#1f97e2" stroke-width="2"><rect x="3" y="8" width="22" height="16"/><path d="M3 8l11 9 11-9"/><circle cx="14" cy="6" r="4"/></svg>
  <div class="kicker">Get In Touch</div>
  <h3>Request a Quote</h3>
  <p class="lead">Itaque earum rerum hic tenetur a sapiente delectus, ut aut reiciendis voluptatibus maiores alias consequatur aut perferendis doloribus asperiores repellat.</p>
  <div class="call"><span class="c"><svg width="20" height="20" viewBox="0 0 24 24" fill="#1f97e2"><path d="M6.6 10.8a15.1 15.1 0 0 0 6.6 6.6l2.2-2.2c.3-.3.7-.4 1-.2 1.1.4 2.3.6 3.6.6.6 0 1 .4 1 1V20c0 .6-.4 1-1 1A17 17 0 0 1 3 4c0-.6.4-1 1-1h3.5c.6 0 1 .4 1 1 0 1.3.2 2.5.6 3.6.1.3 0 .7-.2 1z"/></svg></span><div><small>Call Us Today!</small><b>+1 555 014 7720</b></div></div>
  <div class="field" style="left:356px;top:60px;width:198px;height:46px">First Name</div>
  <div class="field" style="left:578px;top:60px;width:198px;height:46px">Last Name</div>
  <div class="field" style="left:356px;top:120px;width:198px;height:46px">Email</div>
  <div class="field" style="left:578px;top:120px;width:198px;height:46px">Phone Number</div>
  <div class="field" style="left:356px;top:180px;width:420px;height:104px">Message</div>
  <a class="btn submit" href="#">Submit</a>
  <div class="agree"><i></i>I Accept the privacy &amp; terms</div>
  <div class="rule"></div>
</section>

<!-- footer -->
<div class="abs foot-water" role="img" aria-label="Water surface splash with bubbles"></div>
<footer class="abs footer">
  <div class="logo"><span class="dot"></span>BrivoNessé</div>
  <div class="social"><span></span><span></span><span></span><span></span></div>
  <div class="fcol" style="left:427px"><h5>Quick Link</h5><ul><li>Home</li><li>About</li><li>Water Delivery</li><li>Testimonials</li><li>Contact Us</li></ul></div>
  <div class="fcol" style="left:660px"><h5>Help Links</h5><ul><li>FAQ</li><li>Terms of use</li><li>Privacy Policy</li><li>Support Links</li><li>Conditions</li></ul></div>
  <div class="fcol" style="left:892px"><h5>Contact Us</h5>
    <div class="row"><span class="pin"><svg width="14" height="18" viewBox="0 0 14 18" fill="#1f97e2"><path d="M7 0a7 7 0 0 0-7 7c0 5 7 11 7 11s7-6 7-11a7 7 0 0 0-7-7zm0 10a3 3 0 1 1 0-6 3 3 0 0 1 0 6z"/></svg></span><span>BrivoNessé<br>United States</span></div>
    <div class="row"><span class="pin"><svg width="14" height="14" viewBox="0 0 24 24" fill="#1f97e2"><path d="M6.6 10.8a15.1 15.1 0 0 0 6.6 6.6l2.2-2.2c.3-.3.7-.4 1-.2 1.1.4 2.3.6 3.6.6.6 0 1 .4 1 1V20c0 .6-.4 1-1 1A17 17 0 0 1 3 4c0-.6.4-1 1-1h3.5c.6 0 1 .4 1 1 0 1.3.2 2.5.6 3.6.1.3 0 .7-.2 1z"/></svg></span><span style="line-height:32px">+1 555 014 7720</span></div>
    <div class="row"><span class="pin"><svg width="14" height="12" viewBox="0 0 24 20"><path d="M2 2h20v16H2z" fill="#1f97e2"/><path d="M2 2l10 8 10-8" stroke="#fff" stroke-width="2" fill="none"/></svg></span><span style="line-height:32px">info@brivonesse.example</span></div>
  </div>
  <div class="divider"></div>
  <div class="copy">Copyrights@2025.BrivoNessé.All Rights Reserved</div>
</footer>

</body>
</html>
```